BildeVOLD buisnesscard

Hey :) I need a modern buisnesscard for my company BildeVOLD
It most have:
Dagligleder og Fotograf: Henrik Audun Strandvik

Mob: +4791264085
Epost: post@bildevold.example
Adresse: Kvernbakken9, 6040 Fjordvik

Facbook and instagram logo with text BildeVOLD

BildeVOLD logo

It Company

```html
<!DOCTYPE html>
<html lang="no">
<head>
<meta charset="utf-8">
<title>BildeVOLD business card</title>
<link href="https://fonts.googleapis.com/css2?family=Lato:wght@400;700;900&display=swap" rel="stylesheet">
<style>
  :root {
    --stage: #5a5a5c;
    --ink: #111111;
    --paper: #ffffff;
    --brand-grey: #a9a8a9;
    --rule: #c4c4c4;
    --soft-grey: #bdbdbd;
    --swoosh-grey: #c9c9c9;
  }
  * { margin: 0; padding: 0; box-sizing: border-box; }
  html, body { width: 1200px; height: 900px; overflow: hidden; }
  body {
    background: var(--stage);
    font-family: "Lato", Arial, sans-serif;
    display: flex;
    flex-direction: column;
    align-items: center;
    justify-content: center;
    gap: 40px;
  }
  .card {
    position: relative;
    width: 660px;
    height: 377px;
    overflow: hidden;
  }

  /* Front */
  .card-front { background: var(--paper); }
  .front-wordmark {
    position: absolute;
    left: 40px; top: 44px;
    display: flex; align-items: center; gap: 12px;
    color: var(--brand-grey);
    font-weight: 900;
    font-size: 40px;
    letter-spacing: 0.5px;
  }
  .wordmark-square {
    width: 30px; height: 30px;
    background: var(--brand-grey);
  }
  .top-rule {
    position: absolute;
    left: 40px; right: 40px; top: 118px;
    height: 1px; background: var(--rule);
  }
  .contact-list {
    position: absolute;
    left: 40px; top: 132px;
    list-style: none;
    font-size: 15px;
    line-height: 19px;
    color: var(--ink);
  }
  .contact-list li { display: flex; align-items: center; gap: 10px; }
  .contact-icon { width: 11px; height: 11px; flex: none; }
  .person {
    position: absolute;
    right: 40px; top: 192px;
    text-align: right;
  }
  .person-name { font-size: 24px; color: var(--ink); font-weight: 400; }
  .person-title { font-size: 16px; color: var(--soft-grey); margin-top: 2px; }
  .person-rule { height: 1px; background: var(--rule); margin-top: 6px; width: 300px; margin-left: auto; }
  .address {
    position: absolute;
    right: 40px; top: 272px;
    text-align: right;
    font-size: 17px;
    line-height: 22px;
    color: var(--ink);
  }
  .swoosh { position: absolute; left: 0; bottom: 0; width: 660px; height: 130px; }
  .email-band {
    position: absolute;
    right: 40px; bottom: 6px;
    color: var(--paper);
    font-size: 18px;
    line-height: 20px;
    letter-spacing: 0.3px;
  }

  /* Back */
  .card-back {
    background: var(--ink);
    display: flex; align-items: center; justify-content: center;
  }
  .back-wordmark {
    display: flex; align-items: center; gap: 16px;
    color: var(--brand-grey);
    font-weight: 900;
    font-size: 58px;
    letter-spacing: 0.5px;
  }
  .back-wordmark .wordmark-square { width: 44px; height: 44px; }
</style>
</head>
<body>

  <section class="card card-front" aria-label="Business card front">
    <div class="front-wordmark"><span class="wordmark-square"></span>BildeVOLD</div>
    <div class="top-rule"></div>

    <ul class="contact-list">
      <li>
        <svg class="contact-icon" viewBox="0 0 11 11"><rect x="2.5" y="0.5" width="6" height="10" rx="1" fill="none" stroke="#bdbdbd"/></svg>
        +4791264085
      </li>
      <li>
        <svg class="contact-icon" viewBox="0 0 11 11"><rect width="11" height="11" rx="2" fill="#bdbdbd"/></svg>
        BildeVOLD
      </li>
      <li>
        <svg class="contact-icon" viewBox="0 0 11 11"><circle cx="5.5" cy="5.5" r="5.5" fill="#bdbdbd"/></svg>
        BildeVOLD
      </li>
    </ul>

    <div class="person">
      <div class="person-name">Henrik Audun Strandvik</div>
      <div class="person-title">Dagligleder og Fotograf</div>
      <div class="person-rule"></div>
    </div>

    <div class="address">Kvernbakken 9<br>6040 Fjordvik</div>

    <svg class="swoosh" viewBox="0 0 660 130" preserveAspectRatio="none" aria-hidden="true">
      <path d="M0 36 C 150 72, 350 90, 560 97 C 350 93, 150 76, 0 54 Z" fill="#c9c9c9"/>
      <path d="M0 66 C 150 94, 350 100, 500 100 L 660 100 L 660 130 L 0 130 Z" fill="#111111"/>
    </svg>
    <div class="email-band">post@bildevold.example</div>
  </section>

  <section class="card card-back" aria-label="Business card back">
    <div class="back-wordmark"><span class="wordmark-square"></span>BildeVOLD</div>
  </section>

</body>
</html>
```